Business Cards for new orthopaedic surgery practice

My husband and I are starting our own orthopaedic surgery practice. We are looking for a business card that is uniform, but one will have my name/title and the other will have his. You can just create one design with my name on it for now. But when I choose your design as the winning design I will ask that you add another copy with his name/title.

We are looking for classy, simple, elite all in one. We like dark blues/a little gold/yellow. Something that goes with our logo. We want our logo incorporated. Here is all the info you need:
Business name: RV Bone & Vitality Center
Location: 38517 North Willowmere Ave
Palm Verdant, FL 34902
Phone: 954-218-4063
Fax: 954-582-7341
Email: info@myrvbonecare.example

Names: Lydia Vance, M.D.
Board Certified Hand and Upper Extremity Surgeon

Ebo Dansu, M.D.
Board Certified Hip & Knee Replacement/General Orthopaedic Surgeon

Can decide what you want to put on the back. Maybe a slogan:
Steady Hands. Lasting Motion

I am just going to upload our logo. The only thing is if we select you as the winning design, the location, and phone numbers may change. We will need your help to update that once fully solidified.

Industry/Entity Type

Medical

Contact Information for Business Card

Colors
0054AA
0677BA
7BADD7
CADEEF
E8F1F8
0094D4
00A9DD
6FCCEA
C7EBF8
E9F6FB

Requirements
Must have
• class, appeal,
Should not have
• We want to air on the side of masculine if we are looking at masculine vs. feminine feel. But we still want it classy, sophisticated, and something we will love

```html
<!DOCTYPE html>
<html lang="en">
<head>
<meta charset="utf-8">
<title>RV Bone &amp; Vitality Center – Business Card</title>
<link href="https://fonts.googleapis.com/css2?family=Montserrat:wght@400;500;600;700&display=swap" rel="stylesheet">
<style>
  :root {
    --navy: #18275a;
    --navy-deep: #121f4b;
    --gold: #c6963a;
    --gold-light: #deb862;
    --card-light: #f3f4f6;
    --card-mist: #e3e7ec;
    --ink-light: #e8eaf2;
    --page: #e7e4df;
  }
  html, body {
    margin: 0;
    padding: 0;
    width: 1200px;
    height: 887px;
    overflow: hidden;
    background: var(--page);
    font-family: "Montserrat", Arial, sans-serif;
  }
  .business-card {
    position: absolute;
    left: 80px;
    top: 158px;
    width: 1040px;
    height: 570px;
    border-radius: 26px;
    overflow: hidden;
    background: linear-gradient(160deg, var(--card-light) 0%, #ffffff 45%, var(--card-mist) 100%);
    box-shadow: 0 14px 40px rgba(20, 30, 60, 0.18);
  }
  .card-waves {
    position: absolute;
    inset: 0;
  }
  .brand-mark {
    position: absolute;
    left: 56px;
    top: 53px;
    width: 264px;
    height: 264px;
    display: flex;
    align-items: center;
    justify-content: center;
    text-align: center;
  }
  .brand-ring {
    position: absolute;
    inset: 0;
  }
  .brand-name {
    position: relative;
    margin: 0;
    font-size: 25px;
    font-weight: 600;
    line-height: 1.3;
    letter-spacing: 1px;
    color: var(--navy);
    text-transform: uppercase;
  }
  .doctor {
    position: absolute;
    right: 65px;
    top: 52px;
    text-align: right;
  }
  .doctor-name {
    margin: 0 0 6px;
    font-size: 36px;
    font-weight: 700;
    letter-spacing: 1px;
    color: var(--gold);
  }
  .doctor-title {
    margin: 0;
    font-size: 22px;
    font-weight: 400;
    line-height: 28px;
    color: var(--navy);
  }
  .edge-tab {
    position: absolute;
    right: 0;
    top: 62px;
    width: 32px;
    height: 80px;
    background: var(--navy);
    border-radius: 12px 0 0 12px;
  }
  .contact-list {
    position: absolute;
    right: 50px;
    top: 280px;
    margin: 0;
    padding: 0;
    list-style: none;
    text-align: right;
  }
  .contact-item {
    display: flex;
    justify-content: flex-end;
    align-items: center;
    gap: 12px;
    height: 28px;
    font-size: 21px;
    color: var(--ink-light);
  }
  .contact-icon {
    width: 18px;
    height: 18px;
    flex: none;
  }
  .address {
    position: absolute;
    right: 83px;
    top: 415px;
    margin: 0;
    font-style: normal;
    font-size: 21px;
    line-height: 28px;
    text-align: right;
    color: var(--ink-light);
  }
  .slogan {
    position: absolute;
    right: 83px;
    top: 492px;
    margin: 0;
    font-size: 21px;
    font-weight: 600;
    color: var(--gold);
  }
</style>
</head>
<body>
  <main class="business-card">
    <svg class="card-waves" width="1040" height="570" viewBox="0 0 1040 570" aria-hidden="true">
      <defs>
        <linearGradient id="goldSweep" x1="0" y1="0" x2="1" y2="0">
          <stop offset="0" stop-color="#c6963a"/>
          <stop offset="0.5" stop-color="#deb862"/>
          <stop offset="1" stop-color="#b8862e"/>
        </linearGradient>
      </defs>
      <path class="navy-sweep" fill="#18275a"
            d="M0,398 C170,440 340,420 520,322 C360,430 170,475 0,446 Z"/>
      <path class="gold-sweep" fill="url(#goldSweep)"
            d="M0,452 C220,500 430,440 640,328 C780,258 900,228 1010,246 C900,236 790,268 660,340 C440,470 210,530 0,502 Z"/>
      <path class="navy-base" fill="#18275a"
            d="M0,512 C230,528 440,470 620,362 C760,280 890,250 1040,268 L1040,570 L0,570 Z"/>
    </svg>

    <div class="brand-mark">
      <svg class="brand-ring" viewBox="0 0 264 264" aria-hidden="true">
        <circle cx="132" cy="132" r="128" fill="none" stroke="#c6963a" stroke-width="3"/>
      </svg>
      <p class="brand-name">RV Bone &amp;<br>Vitality<br>Center</p>
    </div>

    <div class="edge-tab"></div>

    <header class="doctor">
      <h1 class="doctor-name">LYDIA VANCE, M.D</h1>
      <p class="doctor-title">Board Certified Hand and<br>Upper Extremity Surgeon</p>
    </header>

    <ul class="contact-list">
      <li class="contact-item">954-218-4063
        <svg class="contact-icon" viewBox="0 0 24 24" aria-label="phone"><path fill="#c6963a" d="M6.6 10.8a15.5 15.5 0 0 0 6.6 6.6l2.2-2.2a1 1 0 0 1 1-.25 11.4 11.4 0 0 0 3.6.57 1 1 0 0 1 1 1V20a1 1 0 0 1-1 1A17 17 0 0 1 3 4a1 1 0 0 1 1-1h3.5a1 1 0 0 1 1 1c0 1.250.2 2.45.57 3.57a1 1 0 0 1-.25 1z"/></svg>
      </li>
      <li class="contact-item">954-582-7341
        <svg class="contact-icon" viewBox="0 0 24 24" aria-label="fax"><g fill="none" stroke="#c6963a" stroke-width="2"><rect x="6" y="3" width="12" height="6"/><rect x="3" y="9" width="18" height="9" rx="1"/><rect x="7" y="14" width="10" height="7"/></g></svg>
      </li>
      <li class="contact-item">info@myrvbonecare.example
        <svg class="contact-icon" viewBox="0 0 24 24" aria-label="email"><g fill="none" stroke="#c6963a" stroke-width="2"><rect x="3" y="5" width="18" height="14" rx="1"/><path d="M3 6l9 7 9-7"/></g></svg>
      </li>
      <li class="contact-item">www.myrvbonecare.example
        <svg class="contact-icon" viewBox="0 0 24 24" aria-label="website"><g fill="none" stroke="#c6963a" stroke-width="2"><circle cx="12" cy="12" r="9"/><ellipse cx="12" cy="12" rx="4" ry="9"/><path d="M3 12h18M5 7h14M5 17h14"/></g></svg>
      </li>
    </ul>

    <address class="address">38517 North Willowmere Ave<br>Palm Verdant, FL 34902</address>

    <p class="slogan">Steady Hands. Lasting Motion</p>
  </main>
</body>
</html>
```